Defense contractor needs a roll-up for an exhibition

The booth we have booked has only a size of 3m².
So this will be the centerpiece of the whole booth.
We need a roll-up that attracts visitors and at the same time it should contain already designed graphics. These graphics are giving visitors an overview of our system. So it is necessary to have them exposed in a height that the booth personal can conveniently point with its fingers at them.
For information about our company and product visit:
https://www.brellowtrackline.com/
For designing you should use Adobe Illustrator and the templates provided in the zip file, to guarantee a perfect print.
I have supplied my business card that you can copy the logo. As the company logo will be already at the booth nearby the top of the roll-up, you should not place it there. It can be in the middle or at the bottom.
I have uploaded a picture of the booth. The roll up will be placed at the left of the screen and has a size of 80cm x 200cm

Defense

Defense

Serif

0054AA
0677BA
7BADD7
CADEEF
E8F1F8

• you must use the Adobe Illustrator template to have a good printing result
• company logo on the upper side of the roll-up

```html
<!DOCTYPE html>
<html lang="en">
<head>
<meta charset="utf-8">
<title>Brellow Trackline – Roll-up</title>
<link href="https://fonts.googleapis.com/css2?family=Antonio:wght@600;700&family=Open+Sans:wght@400;700&display=swap" rel="stylesheet">
<style>
  :root {
    --stage: #d9d9db;
    --navy: #1d3a8a;
    --royal: #2746b0;
    --night: #141a4a;
    --dusk-violet: #5a4a9e;
    --dusk-pink: #d49ab8;
    --ink: #000000;
    --white: #ffffff;
    --panel: #e4e8f5;
    --panel-shade: #c9cfe6;
    --rule: rgba(255,255,255,0.55);
  }
  * { box-sizing: border-box; margin: 0; padding: 0; }
  html, body { width: 1200px; height: 900px; overflow: hidden; }
  body {
    background: var(--stage);
    display: flex; align-items: center; justify-content: center;
    font-family: "Open Sans", Arial, sans-serif;
  }
  .rollup {
    position: relative;
    width: 374px; height: 880px;
    overflow: hidden;
    background: linear-gradient(180deg, var(--navy) 0%, var(--royal) 22%, var(--night) 45%, var(--dusk-violet) 62%, var(--dusk-pink) 68%, var(--night) 74%, var(--ink) 80%);
    box-shadow: 0 6px 20px rgba(0,0,0,0.25);
  }
  .header-cut { position: absolute; top: 0; left: 0; width: 374px; height: 180px; }
  .headline {
    position: absolute; top: 28px; left: 0; right: 0;
    text-align: center; color: var(--white);
    font-family: "Antonio", "Arial Narrow", sans-serif; font-weight: 700;
    font-size: 24px; line-height: 27px; letter-spacing: -0.2px;
    text-transform: uppercase; white-space: nowrap;
  }
  .visual {
    position: absolute; left: 17px; width: 340px;
    background: linear-gradient(160deg, var(--panel) 0%, var(--panel-shade) 100%);
  }
  .visual--field { top: 101px; height: 210px; clip-path: polygon(0 38px, 100% 0, 100% 100%, 0 100%); }
  .visual--classroom { top: 382px; height: 190px; }
  .intro {
    position: absolute; top: 326px; left: 17px; width: 340px;
    color: var(--white); font-size: 8.1px; line-height: 11.2px; text-align: justify;
  }
  .skyline {
    position: absolute; left: 0; top: 590px; width: 374px; height: 290px;
    background: linear-gradient(180deg, rgba(0,0,0,0) 0%, var(--ink) 18%);
  }
  .features {
    position: absolute; top: 646px; left: 20px; width: 336px;
    display: grid; grid-template-columns: repeat(4, 1fr);
  }
  .feature {
    height: 66px; display: flex; flex-direction: column; align-items: center; justify-content: flex-end;
    padding-bottom: 6px; color: var(--white);
    font-size: 6.2px; font-weight: 700; line-height: 8.4px; text-align: center; text-transform: uppercase;
    border-left: 1px solid var(--rule);
  }
  .feature:nth-child(4n+1) { border-left: none; }
  .feature:nth-child(-n+4) { border-bottom: 1px solid var(--rule); }
  .feature svg { width: 22px; height: 24px; margin-bottom: 5px; fill: none; stroke: var(--white); stroke-width: 1.4; }
  .brand {
    position: absolute; left: 0; right: 0; top: 812px;
    text-align: center; color: var(--white);
    font-family: "Antonio", "Arial Narrow", sans-serif; font-weight: 700;
    font-size: 26px; letter-spacing: 0.5px; text-transform: uppercase; white-space: nowrap;
  }
</style>
</head>
<body>
  <main class="rollup">
    <svg class="header-cut" viewBox="0 0 374 180" aria-hidden="true">
      <polygon points="374,80 374,130 300,98" fill="#000"/>
      <polygon points="0,137 374,76 374,82 0,143" fill="#fff"/>
    </svg>
    <h1 class="headline">Advanced Combat Training Systems<br>for Realistic Combat Simulation</h1>

    <div class="visual visual--field" role="img" aria-label="Illustration of tanks, range targets and a mobile instructor vehicle with screens"></div>

    <p class="intro">TRAXIS (Tactical Range And eXercise Instrumentation System) allows for a modern approach to duel simulation, firing range training, armored vehicle driving training, and simulation debriefing through an integrated system of sensors, optics, and controls that give soldiers and instructors real-time, real-world vision and data.</p>

    <div class="visual visual--classroom" role="img" aria-label="Illustration of a debriefing classroom with trainees at desks and two wall screens"></div>

    <div class="skyline" role="img" aria-label="Tank silhouette against a dusk sky with grass in the foreground"></div>

    <section class="features">
      <div class="feature"><svg viewBox="0 0 22 24"><rect x="7" y="7" width="8" height="16" rx="1.5"/><circle cx="11" cy="12" r="2"/><path d="M7 4a6 6 0 0 1 8 0M9 5.5a3 3 0 0 1 4 0"/></svg>Remote-control<br>functions</div>
      <div class="feature"><svg viewBox="0 0 22 24"><path d="M2 8h18M4 8a7 7 0 0 0 14 0"/><circle cx="11" cy="14" r="3"/><path d="M11 17v4"/></svg>16 camera systems<br>per vehicle</div>
      <div class="feature"><svg viewBox="0 0 22 24"><rect x="2" y="8" width="18" height="13" rx="2"/><path d="M7 8l2-3h4l2 3"/><circle cx="11" cy="14.5" r="4"/></svg>Optics<br>camera</div>
      <div class="feature"><svg viewBox="0 0 22 24"><rect x="5" y="2" width="12" height="20" rx="1.5"/><path d="M8 7h6M8 11h6M8 15h6M8 19h3"/></svg>Vehicle<br>data</div>
      <div class="feature"><svg viewBox="0 0 22 24"><circle cx="9" cy="10" r="6"/><path d="M13.5 14.5l6 6"/></svg>Full instructor<br>overview</div>
      <div class="feature"><svg viewBox="0 0 22 24"><path d="M13 4a2 2 0 0 1 4 0v11a4 4 0 1 1-4 0z"/><path d="M9 8a4 4 0 0 0 0 8M4 12h2M5 7l1.5 1.5M5 17l1.5-1.5"/></svg>Air-conditioned<br>instructor</div>
      <div class="feature"><svg viewBox="0 0 22 24"><path d="M4 14v-2a7 7 0 0 1 14 0v2M7 10v6M9 8v10M11 6v14M13 8v10M15 10v6"/></svg>Full data<br>recording</div>
      <div class="feature"><svg viewBox="0 0 22 24"><path d="M2 21l9-17 9 17z"/><path d="M11 11v6M8.5 14h5M9 12l4 4M13 12l-4 4"/></svg>All-weather &amp;<br>all-terrain</div>
    </section>

    <p class="brand">Brellow Trackline</p>
  </main>
</body>
</html>
```